Webdesign für Hunde- und Katzenernährungsberatung
Zielgruppe
Hunde und Katzenernährungsberatung, für Menschen, die auch bei ihren Hunden und Katzen auf gesunde, natürliche Ernährung achten wollen, ohne unnötigen Geschmacksverstärker, Zucker, Zusatzstoffe, etc. die gesundheitliche Probleme bei den Tieren verursachen können.
Umstellung auf natürliche, artgerechte Fütterung, teils roh, teils gekocht, angepasst auf Grösse, Rasse, Alter etc., auch speziell für Welpen
Beratung bei:
Übergewicht
Allergien
Unverträglichkeiten
Magen-Darm Problemen
individuelle Ernährungspläne
Selbsthergestellte Kekse, Leckerlies, Snacks, Pralinen und div. Hausmannskost in Einmachgläsern (alles auf Vorbestellung).
Diverse Accessoires
Halsbänder, Leinen, Geschirr aus div. natürlichen Materialien
Lern- und Spielzeug aus Holz und Stoff
div. Zubehör für Tiere, sowie auch für Frauchen und Herrchen
Aufgabenstellung
Die Seite sollte stilvoll aber nicht überfüllt sein und im Retro/Vintage Stil gehalten werden, da das Logo bereits sehr wirksam und eher auffällig ist, dezente Töne im Hintergrund, die Nahrungsmittel werden dann ev. auf Schieferplatten oder unauffälligem Hintergrund platziert. Ich sollte zu einem späteren Zeitpunkt selber Fotos, Links, Texte, etc. einfach dazu fügen können.

```html
<!DOCTYPE html>
<html lang="de">
<head>
<meta charset="utf-8">
<title>Napfwerk – Hunde- und Katzenernährungsberatung</title>
<link rel="stylesheet" href="https://fonts.googleapis.com/css2?family=Kaushan+Script&family=Open+Sans:wght@400;600;700&display=swap">
<style>
  :root {
    --sky: #93c3de;
    --sky-deep: #7fb4d3;
    --white: #ffffff;
    --paper: #f4f4f4;
    --brown: #4a2a1a;
    --rust: #b4621c;
    --amber: #e9aa4c;
    --nav-ink: #3b2a20;
    --slate: #5f6f7c;
    --text-grey: #6b6b6b;
  }
  * { box-sizing: border-box; margin: 0; padding: 0; }
  html, body { width: 1200px; height: 800px; overflow: hidden; background: var(--white); }
  body { font-family: "Open Sans", Arial, sans-serif; position: relative; }

  .site-header {
    position: absolute; left: 0; top: 0; width: 1200px; height: 56px;
    background: var(--white); z-index: 3;
  }
  .brand-badge {
    position: absolute; left: 222px; top: 0; width: 150px; height: 104px;
    background: var(--white); border-radius: 0 0 75px 75px;
    display: flex; flex-direction: column; align-items: center; justify-content: center; gap: 6px;
  }
  .brand-dot { width: 34px; height: 34px; border-radius: 50%; background: var(--sky-deep); }
  .brand-name { font-weight: 700; font-size: 17px; color: var(--sky-deep); letter-spacing: .5px; }

  .main-nav {
    position: absolute; left: 506px; top: 22px;
    display: flex; gap: 14px; font-size: 9px; font-weight: 600; letter-spacing: .3px;
  }
  .main-nav a { color: var(--nav-ink); text-decoration: none; }
  .main-nav a.is-active { color: var(--amber); }

  .hero {
    position: absolute; left: 0; top: 56px; width: 1200px; height: 390px;
    background: var(--sky); border-bottom: 4px solid var(--amber);
  }
  .hero-copy { position: absolute; left: 250px; top: 100px; width: 330px; text-align: center; }
  .hero-rule { height: 2px; background: var(--white); width: 170px; margin: 0 auto 6px; }
  .hero-title {
    font-family: "Kaushan Script", cursive; font-weight: 400;
    font-size: 48px; line-height: 42px; color: var(--brown);
  }
  .hero-title .light { color: var(--white); }
  .hero-sub { margin-top: 8px; font-size: 8px; font-weight: 600; color: var(--brown); letter-spacing: .3px; }
  .hero-button {
    display: inline-block; margin-top: 34px; padding: 5px 26px;
    background: var(--slate); color: var(--white); font-size: 8px; font-weight: 700; letter-spacing: .4px;
  }
  .hero-art {
    position: absolute; left: 590px; top: 50px; width: 430px; height: 340px;
    background: linear-gradient(160deg, #8a5230 0%, #e9a040 55%, #f2b45a 100%);
    border-radius: 180px 180px 0 0;
  }
  .slider-arrow { position: absolute; top: 176px; }
  .slider-arrow.prev { left: 14px; }
  .slider-arrow.next { right: 14px; }

  .welcome {
    position: absolute; left: 0; top: 450px; width: 1200px; height: 350px; background: var(--paper);
  }
  .welcome-photo {
    position: absolute; left: 315px; top: 30px; width: 190px; height: 320px;
    background: linear-gradient(180deg, #d9c08e 0%, #e8c7ae 50%, #cfa98a 100%);
    border-radius: 95px 95px 0 0;
  }
  .welcome-copy { position: absolute; left: 548px; top: 84px; width: 340px; }
  .welcome-title {
    font-family: "Kaushan Script", cursive; font-weight: 400;
    font-size: 27px; line-height: 28px; color: var(--rust);
  }
  .welcome-text { margin-top: 12px; font-size: 8.5px; line-height: 14px; color: var(--text-grey); }
</style>
</head>
<body>
  <header class="site-header">
    <div class="brand-badge">
      <span class="brand-dot"></span>
      <span class="brand-name">Napfwerk</span>
    </div>
    <nav class="main-nav">
      <a class="is-active" href="#">STARTSEITE</a>
      <a href="#">ERNÄHRUNGSBERATUNG</a>
      <a href="#">FUTTER</a>
      <a href="#">ACCESSOIRES</a>
      <a href="#">ONLINESHOP</a>
      <a href="#">KONTAKT</a>
    </nav>
  </header>

  <section class="hero">
    <div class="hero-copy">
      <div class="hero-rule"></div>
      <h1 class="hero-title">Lorem ipsum<br><span class="light">dolor sit amet</span></h1>
      <p class="hero-sub">LOREM IPSUM DOLOR SIT AMET CONSECTETUR ADIPISCING ELIT</p>
      <span class="hero-button">ONLINE SHOP</span>
    </div>
    <div class="hero-art" role="img" aria-label="Illustration einer orangefarbenen Katze und eines braunen Hundes, die nebeneinander sitzen"></div>
    <svg class="slider-arrow prev" width="14" height="20" viewBox="0 0 14 20"><path d="M11 2 L3 10 L11 18" fill="none" stroke="#ffffff" stroke-width="3"/></svg>
    <svg class="slider-arrow next" width="14" height="20" viewBox="0 0 14 20"><path d="M3 2 L11 10 L3 18" fill="none" stroke="#ffffff" stroke-width="3"/></svg>
  </section>

  <section class="welcome">
    <div class="welcome-photo" role="img" aria-label="Porträtfoto der Ernährungsberaterin"></div>
    <div class="welcome-copy">
      <h2 class="welcome-title">Willkommen auf<br>unserer Website</h2>
      <p class="welcome-text">Hier finden Sie bald alles rund um gesunde, natürliche Ernährung für Hund und Katze. Wir beraten Sie gern persönlich und erstellen individuelle Futterpläne für jedes Tier.</p>
    </div>
  </section>
</body>
</html>
```